Clean & Inspiring Web Design Project

Tallowmere Object Works, LLC (also known as T7-Works) is a company which provides 3D printing services and products. The emphasis is on making these products and services available to the mass-market - customers and users who may or may not have prior experience with 3D printing and/or rapid prototyping technologies. We are a start-up company, looking to build a clean and creativity inspiring brand - our site must encourage visitor to engage and make something. Our aim is to help take mere ideas and turn them into tangible items. We want to show a fusion of ideas (e.g. pencil sketches on graph paper) with design tools (e.g. CAD and drafting software) and rapid prototyping (e.g. Kindlo 3D printers, Stereolithography Machines, etc.). We would like the website to appear professional but at the same time easy to navigate and a good balance between text and pictures. The final design should inspire customers to nurture their ideas into real products and communicate our services to our customers. Our site should have the feel of a vibrant social community with the added benefit of tangible physical creations.

Target Market(s)

People with great ideas that need to be designed into a real product

Industry/Entity Type

Printing

Requirements
Must have
• - Website design should include 2 layouts - one for a "landing page" and one for a "content page"
- Website design must incorporate attached company logo (or derivative of this logo)
- Website design should incorporate the menu options shown in the attached PDF UI concept (UI does not necessarily need to look like the provided concept, just include all the clickable elements)
- Website design must portray an innovative and cooperative design environment with a look-and-feel that appeals to both amateur and professional designers.
- Please include pictures, illustrations and photographs (as needed) related to 3D printing, CAD design, conventional drafting, engineering and manufacturing industries.
- Design should support scaling to multiple screen sizes, from tablet computers (e.g. Zelo) to very large screen PCs.
- Design should include Username & Password fields for login or a button to pull up a login popup.
Nice to have
• - Website design could include "Invent", "Make", "Produce" and "Buy" options that slowly cycle through - with appropriate photos / graphics. These "menu options" would also be mouse-over enabled to switch into the appropriate context as the cursor enters that region (e.g. mouse over the "Invent" text would bring up page 2, etc.). (See attached Original UI Thoughts)
Should not have
• Requirements - Should Not Have:
- Website design should not portray a service that is very expensive or complicated - we are a reasonably priced service meant to be friendly with amateur inventors
- Website design should not be overly complicated - please keep it reasonably simple
- Website design should not be overly trendy
- Website design should not use more than 2 font styles, gaudy fonts, etc.
- Website design should not be "campy" or "tacky" - playful is ok, but please keep it elegant
- Website design should not be overly masculine or feminine - we will have both women and men as customers

```html
<!DOCTYPE html>
<html lang="en">
<head>
<meta charset="utf-8">
<title>T7-Works – Why T7</title>
<link rel="stylesheet" href="https://fonts.googleapis.com/css2?family=Source+Sans+3:ital,wght@0,400;0,600;1,400&display=swap">
<style>
:root{
  --sky-top:#dde9f3;
  --sky-mid:#e6eff7;
  --sky-low:#f3f7fb;
  --white:#ffffff;
  --brand-blue:#1d5e93;
  --link-blue:#3b8fd0;
  --nav-grey:#9a9a9a;
  --text:#4a4a4a;
  --tile:#4b4b4b;
  --tile-top:#565656;
  --panel:#cfe2f1;
  --band:#3f3f3f;
  --foot:#2a2a2a;
  --foot-text:#c9c9c9;
  --accent-red:#c8373b;
  --shop:#3a3a3a;
  --icon:#8fa5b8;
  font-family:"Source Sans 3",sans-serif;
}
*{box-sizing:border-box;margin:0;padding:0}
html,body{width:1200px;height:835px;overflow:hidden}
body{position:relative;background:linear-gradient(to bottom,var(--sky-top) 0,var(--sky-top) 115px,var(--sky-mid) 116px,var(--sky-low) 640px,var(--sky-low) 738px);color:var(--text)}
.abs{position:absolute}

/* top utility bar */
.shop-btn{left:816px;top:10px;width:69px;height:25px;border-radius:13px;background:var(--shop);color:#fff;font-size:14px;font-style:italic;line-height:25px;text-align:center;box-shadow:0 1px 2px rgba(0,0,0,.3)}
.util-divider{top:12px;width:1px;height:24px;background:#b9c8d4}
.cart{left:916px;top:10px;font-size:15px;line-height:25px;color:#555;display:flex;align-items:center;gap:9px}
.cart b{color:var(--link-blue);font-weight:400;font-size:17px}
.cart-menu{left:1092px;top:17px}

/* main header */
.header-pill{left:90px;top:56px;width:1020px;height:121px;border-radius:61px;background:var(--white);box-shadow:0 2px 6px rgba(80,110,140,.35),inset 0 -3px 8px rgba(0,0,0,.04)}
.brand{left:140px;top:99px;height:36px;display:flex;align-items:center;gap:10px}
.brand-mark{width:16px;height:16px;background:var(--brand-blue)}
.brand-name{font-size:24px;line-height:36px;font-weight:600;color:var(--brand-blue);white-space:nowrap}
.tagline{left:284px;top:99px;font-size:16px;line-height:22px;color:#8c8c8c;font-weight:600;white-space:nowrap}
.main-nav{left:630px;top:65px;height:106px;display:flex}
.main-nav a{display:block;height:106px;line-height:106px;font-size:16px;font-weight:600;color:var(--nav-grey);text-decoration:none;padding:0 18px}
.main-nav a.active{background:#f5f6f7;color:var(--brand-blue);padding:0 17px}

/* sub navigation */
.sub-nav{left:152px;top:179px;width:896px;height:50px;background:var(--white);display:flex;box-shadow:0 1px 2px rgba(0,0,0,.08)}
.sub-nav a{height:50px;line-height:50px;text-align:center;font-size:16px;color:#555;text-decoration:none;border-right:1px solid #e8ecef}
.sub-nav a:last-child{border-right:none}
.sub-nav a.current{color:var(--brand-blue)}
.sub-nav a.hover{background:#f1f5f8}
.sub-pointer{left:434px;top:229px}

/* content */
.headline{left:93px;top:276px;font-size:24px;font-weight:400;color:var(--brand-blue);letter-spacing:.2px}
.copy{left:92px;top:329px;width:626px;font-size:12.6px;line-height:25px;color:var(--text);text-align:justify}
.copy p+p{margin-top:6px}
.topics{left:90px;top:578px;display:flex;gap:2px}
.topic{width:155px;height:82px;background:linear-gradient(to bottom,var(--tile-top) 0,var(--tile-top) 50%,var(--tile) 50%);color:#f2f2f2;font-size:16px;line-height:23px;display:flex;align-items:center;justify-content:center;text-align:center;box-shadow:0 1px 2px rgba(0,0,0,.25)}

/* team feature */
.team-pill{left:836px;top:295px;width:175px;height:39px;border-radius:20px;background:var(--white);font-size:16px;line-height:39px;text-align:center;color:#333}
.team-pill span{color:var(--accent-red);font-size:20px;margin-left:4px}
.product-photo{left:793px;top:370px;width:256px;height:256px;border-radius:6px;background:radial-gradient(ellipse at 50% 40%,#dfe4ee 0,#b9c4dc 35%,#6a7cb8 60%,rgba(243,247,251,0) 75%)}

/* footer */
.dark-band{left:0;top:738px;width:1200px;height:52px;background:var(--band)}
.foot{left:0;top:790px;width:1200px;height:45px;background:var(--foot)}
.connect-panel{left:88px;top:705px;width:1022px;height:67px;border-radius:4px;background:var(--panel)}
.connect-label{left:127px;top:727px;font-size:17px;color:#222;line-height:24px}
.social{top:725px;width:27px;height:27px;border-radius:2px;background:var(--icon)}
.panel-divider{left:515px;top:713px;width:1px;height:52px;background:#a9c1d6}
.login-label{left:553px;top:727px;font-size:17px;color:#222;line-height:24px}
.field{top:724px;width:145px;height:27px;background:var(--white);border:1px solid #b8cadb;font-size:11px;font-style:italic;color:#aaa;line-height:25px;padding-left:18px}
.login-btn{left:986px;top:725px;width:75px;height:25px;background:#2f2f2f;color:#fff;font-size:15px;line-height:25px;text-align:center;border-radius:2px}
.foot-links{left:90px;top:804px;font-size:13px;color:var(--foot-text);line-height:18px}
.foot-links span{color:#777;margin:0 5px}
.copyright{right:91px;top:804px;font-size:13px;color:var(--foot-text);line-height:18px}
</style>
</head>
<body>

<div class="abs shop-btn">SHOP</div>
<div class="abs util-divider" style="left:899px"></div>
<div class="abs cart">
  <svg width="17" height="15" viewBox="0 0 17 15" aria-hidden="true"><path d="M1 2h3l2 8h8l2-6H5" fill="none" stroke="#555" stroke-width="1.5"/><circle cx="7" cy="13" r="1.3" fill="#555"/><circle cx="13" cy="13" r="1.3" fill="#555"/></svg>
  <span>My Cart - <b>0 items</b></span>
</div>
<div class="abs util-divider" style="left:1077px"></div>
<svg class="abs cart-menu" width="16" height="10" viewBox="0 0 16 10" aria-hidden="true"><path d="M0 0h16L8 10z" fill="var(--link-blue)"/></svg>

<div class="abs header-pill"></div>
<div class="abs brand"><span class="brand-mark"></span><span class="brand-name">T7-Works</span></div>
<div class="abs tagline">What you want.<br>Now!</div>
<nav class="abs main-nav">
  <a class="active" href="#">WHY T7</a>
  <a href="#">DREAMER</a>
  <a href="#">MAKER</a>
  <a href="#">PRODUCER</a>
</nav>

<nav class="abs sub-nav">
  <a class="current" href="#" style="width:207px">About T7</a>
  <a class="hover" href="#" style="width:171px">Dream</a>
  <a href="#" style="width:174px">Make</a>
  <a href="#" style="width:178px">Produce</a>
  <a href="#" style="width:166px">sell</a>
</nav>
<svg class="abs sub-pointer" width="24" height="15" viewBox="0 0 24 15" aria-hidden="true"><path d="M0 0h24L12 15z" fill="#c6d1da"/></svg>

<h1 class="abs headline">EXCEPTEUR SINT OCCAECAT</h1>
<div class="abs copy">
  <p>Sed ut perspiciatis unde omnis iste natus error sit voluptatem accusantium doloremque laudantium, totam rem aperiam, eaque ipsa quae ab illo inventore veritatis et quasi architecto beatae vitae dicta sunt explicabo. Nemo enim ipsam voluptatem quia voluptas sit aspernatur aut odit aut fugit, sed quia consequuntur magni dolores eos qui ratione voluptatem sequi nesciunt. Neque porro quisquam est, incidunt ut labore et dolore magnam aliquam quaerat voluptatem. Ut enim ad minima veniam, quis nostrum exercitationem ullam corporis suscipit laboriosam, nisi ut aliquid ex ea commodi consequatur.</p>
  <p>At vero eos et accusamus et iusto odio dignissimos ducimus qui blanditiis praesentium voluptatum deleniti atque corrupti quos dolores et quas molestias excepturi sint occaecati cupiditate non provident, similique sunt in culpa qui officia deserunt mollitia animi, id est laborum et dolorum fuga</p>
</div>
<div class="abs topics">
  <div class="topic">CAD design</div>
  <div class="topic">Conventional<br>Drafting</div>
  <div class="topic">Engineering</div>
  <div class="topic">Manufacturing<br>Industries</div>
</div>

<div class="abs team-pill">Team T7 - <span>BIOS</span></div>
<div class="abs product-photo" role="img" aria-label="Photo of a pair of white and blue running shoes showing the side and the sole"></div>

<div class="abs dark-band"></div>
<div class="abs foot"></div>
<div class="abs connect-panel"></div>
<div class="abs connect-label">Connect with us :</div>
<div class="abs social" style="left:271px" role="img" aria-label="Social network one"></div>
<div class="abs social" style="left:312px" role="img" aria-label="Social network two"></div>
<div class="abs social" style="left:352px" role="img" aria-label="Social network three"></div>
<div class="abs social" style="left:397px" role="img" aria-label="Video channel"></div>
<svg class="abs" style="left:437px;top:725px" width="27" height="27" viewBox="0 0 27 27" role="img" aria-label="Email"><rect width="27" height="27" rx="2" fill="var(--icon)"/><rect x="6" y="8" width="15" height="11" fill="none" stroke="#fff" stroke-width="1.4"/><path d="M6 8l7.5 6L21 8" fill="none" stroke="#fff" stroke-width="1.4"/></svg>
<div class="abs panel-divider"></div>
<div class="abs login-label">Member Login</div>
<div class="abs field" style="left:678px">Username</div>
<div class="abs field" style="left:832px">Password</div>
<div class="abs login-btn">LOG IN</div>

<div class="abs foot-links">Home<span>|</span>Franchise<span>|</span>Distributers<span>|</span>About us<span>|</span>Cart<span>|</span>Contact Us</div>
<div class="abs copyright">Copyright © 2012 Corvane, LLC. All rights reserved.</div>

</body>
</html>
```